Oil and Gas Exploration and Production company needs a business card design

We need a business card design using our logo and colors in the logo. We want a mainstream design.

```html
<!DOCTYPE html>
<html lang="en">
<head>
<meta charset="utf-8">
<title>Norda Oil &amp; Gas — Business Card</title>
<link rel="stylesheet" href="https://fonts.googleapis.com/css2?family=Roboto+Slab:wght@400;700;900&family=Roboto:wght@300;400&display=swap">
<style>
  :root {
    --stage: #e8e4dd;
    --ink: #141414;
    --ink-soft: #232323;
    --gold: #c9992c;
    --paper: #f5f5f3;
    --light-text: #f1f1f1;
  }
  * { margin: 0; padding: 0; box-sizing: border-box; }
  html, body { width: 1200px; height: 911px; overflow: hidden; }
  body { background: var(--stage); position: relative; font-family: "Roboto", sans-serif; }

  .card {
    position: absolute;
    width: 540px; height: 309px;
    border-radius: 18px;
    overflow: hidden;
    box-shadow: 0 10px 28px rgba(0,0,0,0.22);
  }

  /* Front */
  .card-front { left: 80px; top: 120px; display: flex; }
  .front-brand {
    width: 262px; background: var(--paper);
    display: flex; align-items: center; justify-content: center; gap: 12px;
  }
  .brand-dot { width: 22px; height: 22px; border-radius: 50%; background: var(--gold); flex: none; }
  .brand-name {
    font-family: "Roboto Slab", serif; font-weight: 900;
    color: var(--ink); font-size: 27px; line-height: 1.05; letter-spacing: -0.3px;
  }
  .front-divider { width: 3px; background: var(--gold); }
  .front-info {
    flex: 1;
    background: linear-gradient(160deg, var(--ink-soft), var(--ink) 60%);
    color: var(--light-text);
    padding: 50px 0 0 34px;
  }
  .person-name {
    font-family: "Roboto Slab", serif; font-weight: 700;
    color: var(--gold); font-size: 23px; line-height: 1.1;
  }
  .person-title { font-family: "Roboto Slab", serif; font-size: 13px; margin-top: 4px; }
  .address { font-size: 13px; line-height: 1.45; margin-top: 18px; font-weight: 300; }
  .contact-list { list-style: none; margin-top: 12px; font-size: 13px; font-weight: 300; }
  .contact-list li { display: flex; align-items: center; gap: 9px; line-height: 1.55; }
  .contact-list svg { width: 12px; height: 12px; flex: none; fill: var(--gold); }

  /* Back */
  .card-back { left: 580px; top: 480px; background: var(--gold); }
  .back-url {
    position: absolute; left: 30px; top: 36px;
    writing-mode: vertical-rl;
    color: var(--light-text); font-size: 11px; letter-spacing: 4.5px; font-weight: 400;
  }
  .back-brand {
    position: absolute; inset: 0;
    display: flex; align-items: center; justify-content: center; gap: 16px;
  }
  .back-brand .brand-dot { width: 34px; height: 34px; background: var(--ink); }
  .back-brand .brand-name { font-size: 34px; }
</style>
</head>
<body>

<section class="card card-front" aria-label="Business card front">
  <div class="front-brand">
    <span class="brand-dot"></span>
    <span class="brand-name">Norda<br>Oil &amp; Gas</span>
  </div>
  <div class="front-divider"></div>
  <div class="front-info">
    <h1 class="person-name">Daniel Reyes</h1>
    <p class="person-title">CEO/Founder</p>
    <p class="address">1420 Birchwood Road<br>Harbor Falls, Oregon 97201</p>
    <ul class="contact-list">
      <li><svg viewBox="0 0 12 12"><path d="M2.5 1l2 2.2-1 1.3a7 7 0 0 0 4 4l1.3-1 2.2 2-1.4 1.5C5 10.5 1.5 7 1 2.4z"/></svg>555 210 4816</li>
      <li><svg viewBox="0 0 12 12"><path d="M3 0h6a1 1 0 0 1 1 1v10a1 1 0 0 1-1 1H3a1 1 0 0 1-1-1V1a1 1 0 0 1 1-1zm0 1.5v8h6v-8z"/></svg>555 372 9051</li>
      <li><svg viewBox="0 0 12 12"><path d="M3 0h5v3h2a1 1 0 0 1 1 1v6a1 1 0 0 1-1 1H2a1 1 0 0 1-1-1V4a1 1 0 0 1 1-1h1zm1 1v3h3V1zM3 7h6v1H3z"/></svg>555 684 2307</li>
      <li><svg viewBox="0 0 12 12"><path d="M0 2h12v8H0zm1 1v.5l5 3 5-3V3zm0 2v4h10V5L6 8z"/></svg>info@nordaoilgas.com</li>
      <li><svg viewBox="0 0 12 12"><circle cx="6" cy="6" r="5.5"/><path d="M1 6h10M6 .5c-2.5 3-2.5 8 0 11M6 .5c2.5 3 2.5 8 0 11" stroke="#141414" stroke-width=".8" fill="none"/></svg>www.nordaoilgas.com</li>
    </ul>
  </div>
</section>

<section class="card card-back" aria-label="Business card back">
  <p class="back-url">www.nordaoilgas.com</p>
  <div class="back-brand">
    <span class="brand-dot"></span>
    <span class="brand-name">Norda</span>
  </div>
</section>

</body>
</html>
```